Pop punk gig poster design!

In need of an amazing poster design for a gig We are organising, the genre is pop punk, and will be an all ages gig. I need to it bold, random and capture the eye of any bypasses, and make people want to go to the gig just because the poster is awesome! The event will be called "The great daydream" and will consist of three bands and an acoustic set to open. All the bands are full of energy and create an unreal ambiance during there shows, I would like to capture that in the poster. Open to anything spectacular, the sky is the limit.

• I need to have the name of the event "The Great Daydream"
Band names(in this order):
-Fold the Kite
-Velvet Tuesday
-Milo's Compass
-Tessaly Grovers

Date: Saturday 10th November 2012
Time: 5:15pm
Venue: The Quill, 74 Marrowby street, West End, QLD 4101
Ticket price: $10+bf online
$15 at the door.
Free BBQ

```html
<!DOCTYPE html>
<html lang="en">
<head>
<meta charset="utf-8">
<title>The Great Daydream — Gig Poster</title>
<link rel="stylesheet" href="https://fonts.googleapis.com/css2?family=Audiowide&family=Metal+Mania&family=Cinzel:wght@900&family=Russo+One&family=Exo+2:wght@700&display=swap">
<style>
  :root {
    --wall-light: #f2f2f0;
    --wall-mid: #cfcfcb;
    --wall-dark: #8f8f8b;
    --ink: #0e0e0e;
    --rock-red: #6a1414;
    --rock-red-dark: #220505;
    --band-pale: #e4dfc6;
    --band-shadow: #0c0c0c;
    --guitar-light: #716760;
    --guitar-dark: #3a322d;
    --ornament: rgba(30, 30, 30, 0.32);
    --info-white: #ffffff;
    --ticket-ink: #221c18;
  }
  * { margin: 0; padding: 0; box-sizing: border-box; }
  html, body { width: 848px; height: 1200px; overflow: hidden; background: var(--wall-mid); }

  .poster {
    position: relative;
    width: 848px;
    height: 1200px;
    overflow: hidden;
  }

  .brick-wall {
    position: absolute; inset: 0;
    background:
      radial-gradient(ellipse at 68% 40%, var(--wall-light) 0%, transparent 58%),
      radial-gradient(ellipse at 10% 95%, rgba(0,0,0,0.25) 0%, transparent 50%),
      linear-gradient(180deg, var(--wall-light) 0%, var(--wall-mid) 55%, var(--wall-dark) 100%);
  }

  .ornament {
    position: absolute;
    border-radius: 50%;
    background: radial-gradient(circle, transparent 56%, var(--ornament) 59%, transparent 64%);
  }
  .ornament--top { left: 30px; top: 10px; width: 260px; height: 260px; }
  .ornament--mid { left: 190px; top: 335px; width: 210px; height: 210px; }
  .ornament--right { left: 640px; top: 650px; width: 240px; height: 240px; }
  .ornament--bottom {
    left: 140px; top: 975px; width: 560px; height: 90px; border-radius: 45px;
    background: radial-gradient(ellipse, rgba(30,30,30,0.22) 0%, transparent 70%);
  }

  .guitar {
    position: absolute;
    left: 0; top: 0;
    width: 848px; height: 1200px;
  }

  .event-title {
    position: absolute;
    left: 0; right: 0; top: 84px;
    text-align: center;
    font-family: "Audiowide", sans-serif;
    font-size: 58px;
    letter-spacing: 1px;
    text-transform: uppercase;
    color: var(--ink);
    text-shadow: 0 0 3px #fff, 0 0 7px #fff, 2px 3px 4px rgba(0,0,0,0.35);
    white-space: nowrap;
  }

  .tagline {
    position: absolute;
    left: 20px; top: 196px;
    font-family: "Metal Mania", cursive;
    font-size: 70px;
    letter-spacing: 3px;
    color: var(--rock-red);
    text-transform: uppercase;
    transform: rotate(6deg);
    transform-origin: left top;
    -webkit-text-stroke: 1.5px var(--rock-red-dark);
    text-shadow: 2px 2px 0 #fff, -1px -1px 0 #fff, 4px 5px 5px rgba(0,0,0,0.5);
    white-space: nowrap;
  }

  .lineup { list-style: none; }
  .band {
    position: absolute;
    font-family: "Cinzel", serif;
    font-weight: 900;
    font-size: 54px;
    text-transform: uppercase;
    color: var(--band-pale);
    -webkit-text-stroke: 1px var(--band-shadow);
    text-shadow: 0 0 4px var(--band-shadow), 0 0 8px var(--band-shadow), 0 0 14px var(--band-shadow), 3px 4px 6px rgba(0,0,0,0.6);
    transform: rotate(8deg);
    transform-origin: left top;
    white-space: nowrap;
  }
  .band--1 { left: 293px; top: 362px; }
  .band--2 { left: 272px; top: 466px; }
  .band--3 { left: 246px; top: 566px; }
  .band--4 { left: 222px; top: 676px; }

  .tickets {
    position: absolute;
    right: 10px; top: 872px;
    text-align: right;
    font-family: "Russo One", sans-serif;
    font-size: 29px;
    line-height: 42px;
    text-transform: uppercase;
    color: var(--ticket-ink);
    transform: skewX(-12deg);
    text-shadow: 0 0 3px #fff, 0 0 6px #fff;
    letter-spacing: 1px;
  }
  .tickets-rule {
    position: absolute;
    left: 320px; right: 0; top: 962px;
    height: 2px;
    background: linear-gradient(90deg, transparent, rgba(20,20,20,0.6));
  }

  .extra {
    position: absolute;
    right: 14px; top: 1128px;
    font-family: "Russo One", sans-serif;
    font-size: 34px;
    text-transform: uppercase;
    color: var(--rock-red);
    transform: skewX(-12deg) rotate(-4deg);
    text-shadow: 0 0 3px #fff, 0 0 7px #fff;
    letter-spacing: 1px;
  }

  .details {
    position: absolute;
    left: 34px; top: 1008px;
    font-family: "Exo 2", sans-serif;
    font-weight: 700;
    font-size: 27px;
    line-height: 42px;
    text-transform: uppercase;
    color: var(--info-white);
    text-shadow: 1px 1px 2px rgba(0,0,0,0.8), 0 0 6px rgba(0,0,0,0.4);
  }
</style>
</head>
<body>
<main class="poster">
  <div class="brick-wall" role="img" aria-label="Grey whitewashed brick wall background"></div>

  <div class="ornament ornament--top" role="img" aria-label="Faint swirl flourish"></div>
  <div class="ornament ornament--mid" role="img" aria-label="Faint swirl flourish"></div>
  <div class="ornament ornament--right" role="img" aria-label="Faint swirl flourish"></div>
  <div class="ornament ornament--bottom" role="img" aria-label="Faint filigree flourish"></div>

  <svg class="guitar" viewBox="0 0 848 1200" role="img" aria-label="Large textured electric guitar silhouette angled across the poster">
    <defs>
      <linearGradient id="guitarTone" x1="0" y1="1" x2="1" y2="0">
        <stop offset="0" stop-color="var(--guitar-dark)"/>
        <stop offset="1" stop-color="var(--guitar-light)"/>
      </linearGradient>
    </defs>
    <rect x="-40" y="460" width="960" height="230" rx="115" fill="url(#guitarTone)" opacity="0.9" transform="rotate(-40 440 575)"/>
  </svg>

  <h1 class="event-title">The Great Daydream</h1>
  <p class="tagline">Let us rock....</p>

  <ul class="lineup">
    <li class="band band--1">Fold the Kite</li>
    <li class="band band--2">Velvet Tuesday</li>
    <li class="band band--3">Milo's Compass</li>
    <li class="band band--4">Tessaly Grovers</li>
  </ul>

  <p class="tickets">Ticket price: $10+bf online<br>$15 at the door</p>
  <div class="tickets-rule"></div>

  <p class="details">
    Date: Saturday 10th November 2012<br>
    Time: 5:15pm<br>
    Venue: The Quill, 74 Marrowby street,<br>
    West End, QLD 4101
  </p>

  <p class="extra">Free BBQ!</p>
</main>
</body>
</html>
```